Design a homepage graphic to show a system journey

We have a software package for parents to update student information and manage school excursions we have attached a concept we like but are open to other ideas so long as they fit the following criteria.
1 It needs to be landscape across the page
2. They are showing a series of processes, each step has its own colour, see below
2.1 The first process is a parent updating their own and students information and approving excursions
2.2 The school then creates and manages the excursion this includes a compliance component
2.3 The school conducts the activity it should show some activity type pictures
2.4 Students return safely to school
3 There can be text boxes within the image to clarify functionality
4. The picture should make anyone watching it understand there is a series of
linked processes the system provides i.e. a journey
There should be the ability to click on each component to link to a specific part of the pager lower down, e.g if the person wanted to look at the school part by clicking on the school it would take them to more information, that information already exists so is not required.
Please review the attached concept diagram and use this a potential guide.
Schools
1 page

```html
<!DOCTYPE html>
<html lang="en">
<head>
<meta charset="utf-8">
<title>System Journey</title>
<link rel="stylesheet" href="https://fonts.googleapis.com/css2?family=Roboto:wght@700;900&display=swap">
<style>
  :root{
    --bg:#f3f3f3;
    --title:#0d5a8e;
    --label:#2a2a2a;
    --road:#3b3b3b;
    --road-edge:#d9d9d9;
    --lane:#ffffff;
    --parent:#1d5a8a;
    --student:#1b90d7;
    --approve:#6b9b3a;
    --accept:#b6cf2b;
    --manage:#edc100;
    --takes:#ef8b22;
    --conduct:#d8262b;
    --return:#d0216f;
    --city-top:#e6f5ec;
    --city-bottom:#a9d6b4;
    --grass:#7db653;
  }
  html,body{margin:0;padding:0;overflow:hidden;background:var(--bg);}
  .journey{width:1200px;height:712px;display:block;}
  .journey-title{font-family:"Roboto",Arial,sans-serif;font-weight:900;font-size:58px;fill:var(--title);letter-spacing:1px;}
  .step-label{font-family:"Roboto",Arial,sans-serif;font-weight:700;font-size:21px;fill:var(--label);}
  .road-edge{fill:none;stroke:var(--road-edge);stroke-width:54;stroke-linecap:round;stroke-linejoin:round;}
  .road-surface{fill:none;stroke:var(--road);stroke-width:42;stroke-linecap:round;stroke-linejoin:round;}
  .road-lane{fill:none;stroke:var(--lane);stroke-width:3;stroke-dasharray:14 10;}
  .pin-face{fill:#fff;}
  .pin-icon{opacity:.35;}
  .step-link{cursor:pointer;}
  .step-link:hover .pin-body{filter:brightness(1.08);}
</style>
</head>
<body>
<svg class="journey" viewBox="0 0 1407 835" xmlns="http://www.w3.org/2000/svg">
  <defs>
    <linearGradient id="cityTone" x1="0" y1="0" x2="0" y2="1">
      <stop offset="0" stop-color="var(--city-top)"/>
      <stop offset="0.8" stop-color="var(--city-bottom)"/>
      <stop offset="1" stop-color="var(--grass)"/>
    </linearGradient>
  </defs>

  <rect class="backdrop" width="1407" height="835" fill="var(--bg)"/>

  <text class="journey-title" x="703" y="82" text-anchor="middle">SYSTEM JOURNEY</text>

  <rect class="cityscape" x="0" y="672" width="1407" height="163" fill="url(#cityTone)" role="img" aria-label="Light green city skyline with a row of trees along the grass"/>

  <g class="road">
    <path class="road-edge" d="M-10,455 C90,470 80,655 175,655 C290,655 250,305 340,305 C410,305 390,440 470,440 L540,440 C610,440 560,590 650,590 C760,590 700,210 850,210 C950,210 940,505 1040,505 L1150,505 C1220,505 1190,635 1280,635 L1420,640"/>
    <path class="road-surface" d="M-10,455 C90,470 80,655 175,655 C290,655 250,305 340,305 C410,305 390,440 470,440 L540,440 C610,440 560,590 650,590 C760,590 700,210 850,210 C950,210 940,505 1040,505 L1150,505 C1220,505 1190,635 1280,635 L1420,640"/>
    <path class="road-lane" d="M-10,455 C90,470 80,655 175,655 C290,655 250,305 340,305 C410,305 390,440 470,440 L540,440 C610,440 560,590 650,590 C760,590 700,210 850,210 C950,210 940,505 1040,505 L1150,505 C1220,505 1190,635 1280,635 L1420,640"/>
  </g>

  <rect class="start-flag" x="4" y="385" width="46" height="62" rx="6" fill="#dcd7c9" role="img" aria-label="Start flag on a green patch"/>
  <rect class="finish-flag" x="1198" y="543" width="66" height="68" rx="6" fill="#dcd7c9" role="img" aria-label="Finish flag on a green patch"/>
  <rect class="home-scene" x="300" y="365" width="72" height="72" rx="8" fill="#f1d9c6" role="img" aria-label="Family home with trees"/>
  <rect class="school-house" x="820" y="278" width="72" height="78" rx="8" fill="#dbe9f2" role="img" aria-label="School building"/>
  <rect class="cyclist" x="806" y="108" width="98" height="88" rx="10" fill="#e2ecd2" role="img" aria-label="Student riding a bicycle"/>
  <rect class="cyclist" x="1076" y="400" width="98" height="90" rx="10" fill="#e2ecd2" role="img" aria-label="Student riding a bicycle"/>

  <!-- Steps -->
  <a class="step-link" href="#parent-information">
    <g transform="translate(172,557)">
      <path class="pin-body" d="M-43,25 A50,50 0 1 1 43,25 L0,70 Z" fill="var(--parent)"/>
      <circle class="pin-face" r="35"/>
      <circle class="pin-icon" r="24" fill="var(--parent)" role="img" aria-label="Parents icon"/>
    </g>
    <text class="step-label" x="167" y="710" text-anchor="middle">PARENT</text>
    <text class="step-label" x="167" y="740" text-anchor="middle">INFORMATION</text>
  </a>

  <a class="step-link" href="#student-information">
    <g transform="translate(335,213)">
      <path class="pin-body" d="M-43,25 A50,50 0 1 1 43,25 L0,70 Z" fill="var(--student)"/>
      <circle class="pin-face" r="35"/>
      <circle class="pin-icon" r="24" fill="var(--student)" role="img" aria-label="Student icon"/>
    </g>
    <text class="step-label" x="260" y="207" text-anchor="end">STUDENT</text>
    <text class="step-label" x="260" y="237" text-anchor="end">INFORMATION</text>
  </a>

  <a class="step-link" href="#approving-excursion">
    <g transform="translate(480,340)">
      <path class="pin-body" d="M-43,25 A50,50 0 1 1 43,25 L0,70 Z" fill="var(--approve)"/>
      <circle class="pin-face" r="35"/>
      <circle class="pin-icon" r="24" fill="var(--approve)" role="img" aria-label="Approval stamp icon"/>
    </g>
    <text class="step-label" x="476" y="493" text-anchor="middle">APPROVING</text>
    <text class="step-label" x="476" y="523" text-anchor="middle">EXCURSION</text>
  </a>

  <a class="step-link" href="#school-accepts">
    <g transform="translate(660,490)">
      <path class="pin-body" d="M-43,25 A50,50 0 1 1 43,25 L0,70 Z" fill="var(--accept)"/>
      <circle class="pin-face" r="35"/>
      <circle class="pin-icon" r="24" fill="var(--accept)" role="img" aria-label="School icon"/>
    </g>
    <text class="step-label" x="658" y="643" text-anchor="middle">SCHOOL ACCEPTS</text>
    <text class="step-label" x="658" y="673" text-anchor="middle">ALL THE UPDATE</text>
  </a>

  <a class="step-link" href="#school-manages">
    <g transform="translate(705,222)">
      <path class="pin-body" d="M-43,25 A50,50 0 1 1 43,25 L0,70 Z" fill="var(--manage)"/>
      <circle class="pin-face" r="35"/>
      <circle class="pin-icon" r="24" fill="var(--manage)" role="img" aria-label="Books and graduation cap icon"/>
    </g>
    <text class="step-label" x="637" y="219" text-anchor="end">SCHOOL MANAGES</text>
    <text class="step-label" x="637" y="249" text-anchor="end">THE EXCURSION</text>
  </a>

  <a class="step-link" href="#school-takes-children">
    <g transform="translate(1013,225)">
      <path class="pin-body" d="M-43,25 A50,50 0 1 1 43,25 L0,70 Z" fill="var(--takes)"/>
      <circle class="pin-face" r="35"/>
      <circle class="pin-icon" r="24" fill="var(--takes)" role="img" aria-label="Child with building blocks icon"/>
    </g>
    <text class="step-label" x="1082" y="219">SCHOOL TAKES</text>
    <text class="step-label" x="1082" y="249">THE CHILDREN TO</text>
    <text class="step-label" x="1082" y="279">THE EXCURSION</text>
  </a>

  <a class="step-link" href="#school-conducts-activity">
    <g transform="translate(1062,402)">
      <path class="pin-body" d="M-43,25 A50,50 0 1 1 43,25 L0,70 Z" fill="var(--conduct)"/>
      <circle class="pin-face" r="35"/>
      <circle class="pin-icon" r="24" fill="var(--conduct)" role="img" aria-label="Phone and message icon"/>
    </g>
    <text class="step-label" x="1057" y="557" text-anchor="middle">SCHOOL CONDUCTS</text>
    <text class="step-label" x="1057" y="587" text-anchor="middle">ACTIVITY</text>
  </a>

  <a class="step-link" href="#students-return">
    <g transform="translate(1300,540)">
      <path class="pin-body" d="M-43,25 A50,50 0 1 1 43,25 L0,70 Z" fill="var(--return)"/>
      <circle class="pin-face" r="35"/>
      <circle class="pin-icon" r="24" fill="var(--return)" role="img" aria-label="School and home icon"/>
    </g>
    <text class="step-label" x="1297" y="693" text-anchor="middle">STUDENTS RETURN</text>
    <text class="step-label" x="1297" y="723" text-anchor="middle">TO SCHOOL</text>
  </a>
</svg>
</body>
</html>
```